BorrowNest Website design, we are a home loan / lending company

We are a finance broking company that can do mortgages / home loans, Car Loans, Commercial Loans, SMSF Loans, Business Loans, Personal Loans
We are looking for a simple website, not too busy, easy to navigate, something that prompts customers to action or call us.
I like the simplicity of the following websites:
https://www.velkarafinance.com.au/ - I like this website front page. I was thinking I have my logo, the one with the black background appear , then the toolbar at the top perhaps?
https://trevix.com.au/business-loans# - on this page there are images under finance that works for you that I like that concept.
https://dunmerel.com.au/contact/ - I like the Make an Appointment page
https://trevix.com.au/about-us - Simple but effective page design

Target Market(s)

Home Loan Customer

Industry/Entity Type

Finance / Home Loans

Coding

Coded - Design and coding required

Number of Pages Required

5+ page

Font styles to use
Serif

Colors
0094D4
00A9DD
6FCCEA
C7EBF8
E9F6FB

Requirements
Must have
• The following Heading s - Contact Us, About Us, Our People, Make an Appointment, Loan Options, Calculators, Reviews. I want to use the Logo colours I have in the zip files I uploaded.
Nice to have
• Simple clean design

```html
<!DOCTYPE html>
<html lang="en">
<head>
<meta charset="utf-8">
<title>BorrowNest – Home Loans</title>
<link href="https://fonts.googleapis.com/css2?family=Mulish:wght@400;600;700;800;900&display=swap" rel="stylesheet">
<style>
:root{
  --blue:#0094D4;
  --blue-2:#00A9DD;
  --sky:#6FCCEA;
  --ice:#C7EBF8;
  --mist:#E9F6FB;
  --ink:#1d1d1f;
  --text:#444;
  --navy:#0b1130;
  --white:#fff;
  --line:#cfe3ec;
}
*{box-sizing:border-box;margin:0;padding:0}
html,body{width:1200px;height:3530px;overflow:hidden}
body{font-family:'Mulish',sans-serif;color:var(--text);background:var(--white);position:relative}
.abs{position:absolute}
.btn{display:inline-block;background:var(--blue);color:var(--white);font-weight:800;font-size:13px;padding:8px 14px;text-decoration:none}
.accent{color:var(--blue)}

/* header */
.site-header{left:0;top:0;width:1200px;height:99px}
.brand{font-weight:800;font-size:40px;color:var(--ink);letter-spacing:-1px}
.site-header .brand{left:130px;top:18px}
.call{left:708px;top:16px;display:flex;align-items:center;gap:12px}
.call .sep{width:1px;height:34px;background:#bbb}
.call small{display:block;font-size:11px;color:var(--ink)}
.call strong{font-size:15px;color:var(--ink);font-weight:700}
.appt{left:890px;top:18px;font-size:14px;padding:7px 14px}
.main-nav{left:449px;top:61px;display:flex;gap:24px;font-size:14px;font-weight:800;color:var(--ink)}
.main-nav span{padding:2px 0}
.main-nav .active{background:var(--blue);color:var(--white);padding:2px 6px;margin-right:-4px}

/* hero */
.hero{left:0;top:99px;width:1200px;height:561px;background:linear-gradient(180deg,#d9c6ae 0%,#cbb79a 35%,#8d8a5c 70%,#6b7a3e 100%)}
.hero-card{left:130px;top:352px;width:381px;height:201px;background:rgba(255,255,255,.82);padding:26px 38px}
.hero-card h1{font-size:36px;font-weight:900;color:var(--ink);line-height:1}
.hero-card p{font-size:15px;color:#333;margin:14px 0 18px;line-height:1.4}
.dots{left:567px;top:624px;display:flex;gap:4px}
.dots i{width:8px;height:8px;background:var(--white);display:block}
.dots i.on{background:var(--blue)}

/* loan cards */
.loan-card{width:299px;height:218px;border:1px solid var(--sky);box-shadow:0 2px 6px rgba(0,148,212,.12);background:var(--white);padding:28px 18px 0 104px}
.loan-card .icon{position:absolute;left:18px;top:36px;width:70px;height:70px;border-radius:50%;background:var(--mist);display:flex;align-items:center;justify-content:center}
.loan-card h3{font-size:16px;font-weight:800;color:var(--ink);margin-bottom:10px}
.loan-card p{font-size:11.5px;line-height:1.25;color:var(--text)}
.loan-card .btn{margin:15px 0 0 1px;font-size:11.5px;padding:6px 8px}
.loan-card.featured{background:var(--blue);border-color:var(--blue)}
.loan-card.featured h3,.loan-card.featured p{color:var(--white)}
.loan-card.featured .icon{background:var(--white)}
.loan-card.featured .btn{background:var(--white);color:var(--blue)}

.divider{left:0;width:1200px;height:7px;border-top:1.5px solid #c9dde6;border-bottom:1.5px solid #c9dde6}

/* about */
.photo{background:linear-gradient(135deg,#b9c2c9,#6d7680)}
.about-text{left:660px;top:1308px;width:408px}
.about-text h2{font-size:28px;font-weight:800;line-height:1.25}
.about-text h2 span{display:block;color:var(--ink)}
.about-text h2 span.accent{color:var(--blue)}
.rule{width:55px;height:3px;background:var(--blue);margin:16px 0 26px}
.about-text p{font-size:13.5px;line-height:1.5;text-align:justify}
.about-text .btn{margin-top:26px;font-size:14px;padding:9px 16px}

/* ready */
.ready-photo{left:0;top:1774px;width:1200px;height:541px;background:linear-gradient(120deg,#e7ddd2 0%,#a89a8d 45%,#5d5048 100%);clip-path:polygon(100% 0,100% 100%,0 100%,0 95%,35% 77%,57% 56%,57% 33%)}
.ready-text{left:130px;top:1818px;width:430px}
.ready-text h2{font-size:28px;font-weight:800;color:var(--ink)}
.ready-text .rule{margin:4px 0 42px;width:120px}
.ready-text p{font-size:13.5px;line-height:1.5;color:#333}
.apply-box{left:133px;top:2018px;width:420px;height:155px;border:2px solid var(--blue);padding:18px 35px;background:var(--white)}
.apply-box h3{font-size:21px;font-weight:800;color:var(--blue)}
.apply-box p{font-size:13px;line-height:1.4;margin:8px 0 12px;color:#333}

/* why */
.why-text{left:666px;top:2362px;width:410px}
.why-text h2{font-size:28px;font-weight:800;color:var(--ink)}
.why-text .sub{font-size:14px;color:#333;margin-top:2px}
.why-text .rule{margin:12px 0 0}
.step{left:666px;width:400px}
.step .num{position:absolute;left:0;top:0;width:52px;height:52px;border-radius:50%;background:var(--sky);color:var(--white);font-size:26px;display:flex;align-items:center;justify-content:center}
.step h4{margin-left:75px;font-size:16px;font-weight:800;color:var(--ink)}
.step p{margin:10px 0 0 77px;font-size:11.5px;line-height:1.4;color:#333}
.step-line{left:692px;top:2528px;height:245px;border-left:1px dashed var(--sky)}

/* reviews */
.reviews-title{left:0;top:2962px;width:1200px;text-align:center}
.reviews-title h2{font-size:28px;font-weight:800;color:var(--ink)}
.reviews-title .rule{margin:10px auto 0;width:34px}
.review{width:300px;height:230px;border:1px solid #ddd;padding:22px 26px;background:var(--white)}
.review .who{display:flex;align-items:center;gap:8px}
.review .avatar{width:26px;height:26px;border-radius:50%;background:#8a9098}
.review .who b{display:block;font-size:12px;color:var(--ink);font-weight:800}
.review .who small{font-size:12px;color:#333}
.review .stars{color:#f5a623;font-size:16px;letter-spacing:1px;margin:8px 0 10px}
.review p{font-size:11.5px;line-height:1.5;text-align:justify;color:#333}
.arrow{top:3165px}

/* footer */
.site-footer{left:0;top:3343px;width:1200px;height:187px;background:var(--navy);color:var(--white)}
.site-footer .brand{position:absolute;left:130px;top:50px;color:var(--white)}
.follow{position:absolute;right:132px;top:42px;display:flex;align-items:center;gap:12px;font-size:13px}
.follow i{display:block;width:24px;height:24px;background:var(--blue)}
.foot-nav{position:absolute;right:132px;top:90px;display:flex;gap:22px;font-size:14px}
.copy{position:absolute;left:0;width:1200px;top:153px;text-align:center;font-size:11.5px}
</style>
</head>
<body>

<header class="site-header abs">
  <div class="brand abs">BorrowNest</div>
  <div class="call abs">
    <svg width="22" height="22" viewBox="0 0 24 24" fill="none" stroke="#0094D4" stroke-width="1.6"><path d="M5 3h4l2 5-2.5 1.5a11 11 0 0 0 6 6L16 13l5 2v4a2 2 0 0 1-2 2A16 16 0 0 1 3 5a2 2 0 0 1 2-2z"/></svg>
    <span class="sep"></span>
    <div><small>Call us</small><strong>+1 800 555 0199</strong></div>
  </div>
  <a class="btn appt abs">Make an Appointment</a>
  <nav class="main-nav abs">
    <span class="active">Home</span><span>About Us</span><span>Our People</span><span>Loan Options</span><span>Calculators</span><span>Reviews</span><span>Contact Us</span>
  </nav>
</header>

<section class="hero abs" role="img" aria-label="Couple embracing in a field looking toward a new family house at sunset"></section>
<div class="hero-card abs">
  <h1>HOME <span class="accent">LOANS</span></h1>
  <p>Lorem Ipsum is simply dummy text of the prin ting and typesetting industry.</p>
  <a class="btn">Read More</a>
</div>
<div class="dots abs"><i></i><i></i><i class="on"></i><i></i><i></i></div>

<div class="loan-card abs" style="left:130px;top:706px">
  <div class="icon"><svg width="38" height="38" viewBox="0 0 40 40" fill="none" stroke="#0094D4" stroke-width="1.8"><path d="M4 20L20 6l16 14"/><path d="M9 16v18h22V16"/><rect x="13" y="20" width="6" height="6"/><rect x="22" y="20" width="6" height="6"/></svg></div>
  <h3>Home Loans</h3>
  <p>There are many variations of passages of Lorem Ipsum avail able, but the majority have suff ered alteration in some form, by injected humour.</p>
  <a class="btn">Read More</a>
</div>
<div class="loan-card featured abs" style="left:451px;top:706px">
  <div class="icon"><svg width="40" height="40" viewBox="0 0 40 40" fill="none" stroke="#0094D4" stroke-width="1.8"><path d="M6 24l3-8h22l3 8v5H6z"/><circle cx="12" cy="29" r="3"/><circle cx="28" cy="29" r="3"/><path d="M11 16l2-4h14l2 4"/></svg></div>
  <h3>Car Loans</h3>
  <p>There are many variations of passages of Lorem Ipsum avail able, but the majority have suff ered alteration in some form, by injected humour.</p>
  <a class="btn">Read More</a>
</div>
<div class="loan-card abs" style="left:771px;top:706px">
  <div class="icon"><svg width="38" height="38" viewBox="0 0 40 40" fill="none" stroke="#0094D4" stroke-width="1.8"><rect x="9" y="6" width="22" height="29"/><path d="M14 12h4M22 12h4M14 18h4M22 18h4M14 24h4M22 24h4M18 35v-5h4v5"/></svg></div>
  <h3>Commercial Loans</h3>
  <p>There are many variations of passages of Lorem Ipsum avail able, but the majority have suff ered alteration in some form, by injected humour.</p>
  <a class="btn">Read More</a>
</div>
<div class="loan-card abs" style="left:130px;top:948px">
  <div class="icon"><svg width="38" height="38" viewBox="0 0 40 40" fill="none" stroke="#0094D4" stroke-width="1.8"><path d="M6 20L20 8l14 12"/><path d="M10 17v14h20V17"/><path d="M16 27l8-8"/><circle cx="16.5" cy="20" r="1.5"/><circle cx="23.5" cy="26" r="1.5"/></svg></div>
  <h3>SMSF Loans</h3>
  <p>There are many variations of passages of Lorem Ipsum avail able, but the majority have suff ered alteration in some form, by injected humour.</p>
  <a class="btn">Read More</a>
</div>
<div class="loan-card abs" style="left:451px;top:948px">
  <div class="icon"><svg width="36" height="36" viewBox="0 0 40 40" fill="none" stroke="#0094D4" stroke-width="2"><rect x="6" y="13" width="28" height="20" rx="2"/><path d="M15 13V9h10v4M6 21h28"/></svg></div>
  <h3>Business Loans</h3>
  <p>There are many variations of passages of Lorem Ipsum avail able, but the majority have suff ered alteration in some form, by injected humour.</p>
  <a class="btn">Read More</a>
</div>
<div class="loan-card abs" style="left:771px;top:948px">
  <div class="icon"><svg width="36" height="36" viewBox="0 0 40 40" fill="#0094D4"><circle cx="20" cy="12" r="7"/><path d="M6 36c0-9 6-14 14-14s14 5 14 14z"/></svg></div>
  <h3>Personal Loans</h3>
  <p>There are many variations of passages of Lorem Ipsum avail able, but the majority have suff ered alteration in some form, by injected humour.</p>
  <a class="btn">Read More</a>
</div>

<div class="divider abs" style="top:1238px"></div>

<div class="photo abs" style="left:131px;top:1310px;width:281px;height:227px;background:linear-gradient(135deg,#9aa6ae,#4f5963)" role="img" aria-label="Smiling couple reviewing loan documents together on a sofa"></div>
<div class="photo abs" style="left:423px;top:1310px;width:196px;height:377px;background:linear-gradient(180deg,#a9b2b8,#e9ecee)" role="img" aria-label="Two business professionals walking in an office"></div>
<div class="photo abs" style="left:131px;top:1549px;width:143px;height:133px;background:linear-gradient(135deg,#7d8a96,#b7c3cc)" role="img" aria-label="Hands working over financial charts on a desk"></div>
<div class="photo abs" style="left:282px;top:1549px;width:130px;height:133px;background:linear-gradient(135deg,#9ab2c0,#d9e6ec)" role="img" aria-label="Pen pointing at printed financial graphs"></div>
<div class="about-text abs">
  <h2><span class="accent">About Us</span><span>BorrowNest</span></h2>
  <div class="rule"></div>
  <p>Sed ut perspiciatis unde omnis iste natus error sit voluptatem accusantium doloremque laudantium, totam rem aperiam, eaque ipsa quae ab illo inventore veritatis et quasi architecto beatae vitae dicta sunt explicabo. Nemo enim ipsam voluptatem quia voluptas sit aspernatur aut odit aut fugit, sed quia consequuntur magni dolores eos qui ratione voluptatem sequi nesciunt. Neque porro quisquam est, qui dolorem ipsum quia dolor sit amet, consectetur adipisci velit, sed quia non numquam eius modi tempora incidunt ut labore et dolore magnam aliquam quaerat voluptatem. Ut enim ad minima veniam.</p>
  <a class="btn">Read More</a>
</div>

<div class="divider abs" style="top:1758px"></div>

<div class="ready-photo abs" role="img" aria-label="Two people at a laptop pointing at bar charts beside a coffee cup"></div>
<div class="ready-text abs">
  <h2><span class="accent">Ready to</span> get started?</h2>
  <div class="rule"></div>
  <p>Sed ut perspiciatis unde omnis iste natus error sit voluptatem accu santium doloremque laudantium, totam rem aperiam, eaque ipsa quae ab illo inventore veritatis et quasi architecto beatae vitae dicta sunt explicabo. Nemo enim ipsam voluptatem.</p>
</div>
<div class="apply-box abs">
  <h3>How do I apply?</h3>
  <p>Nemo enim ipsam voluptatem quia voluptas<br>sit aspernatur aut odit aut fugit.</p>
  <a class="btn">Read More</a>
</div>

<div class="photo abs" style="left:131px;top:2367px;width:488px;height:469px;background:linear-gradient(135deg,#dfe3e5,#aab3b9 60%,#e8d7d2)" role="img" aria-label="Adviser shaking hands with a client across a desk with a piggy bank"></div>
<div class="why-text abs">
  <h2><span class="accent">Why</span> Choose us</h2>
  <div class="sub">IT'S AS SIMPLE AS 1, 2, 3.</div>
  <div class="rule"></div>
</div>
<div class="step-line abs"></div>
<div class="step abs" style="top:2476px"><div class="num">1</div><h4>We do all the hard work for you.</h4><p>Lorem ipsum dolor sit amet, consectetur adipiscing elit, sed do eiusmod tempor incididunt ut labore et dolore magna aliqua. Ut enim ad minim veniam, quis nostrud exercitation ullamco laboris nisi ut aliquip ex ea</p></div>
<div class="step abs" style="top:2608px"><div class="num">2</div><h4>We save your credit rating.</h4><p>Lorem ipsum dolor sit amet, consectetur adipiscing elit, sed do eiusmod tempor incididunt ut labore et dolore magna aliqua. Ut enim ad minim veniam, quis nostrud exercitation ullamco laboris nisi ut aliquip ex ea</p></div>
<div class="step abs" style="top:2748px"><div class="num">3</div><h4>We offer ongoing support</h4><p>Lorem ipsum dolor sit amet, consectetur adipiscing elit, sed do eiusmod tempor incididunt ut labore et dolore magna aliqua. Ut enim ad minim veniam, quis nostrud exercitation ullamco laboris nisi ut aliquip ex ea</p></div>

<div class="divider abs" style="top:2914px"></div>

<div class="reviews-title abs"><h2><span class="accent">Customer</span> Reviews</h2><div class="rule"></div></div>
<svg class="arrow abs" style="left:76px" width="14" height="26" viewBox="0 0 14 26" fill="none" stroke="#888" stroke-width="2"><path d="M12 2L2 13l10 11"/></svg>
<svg class="arrow abs" style="left:1102px" width="14" height="26" viewBox="0 0 14 26" fill="none" stroke="#888" stroke-width="2"><path d="M2 2l10 11L2 24"/></svg>
<div class="review abs" style="left:130px;top:3061px"><div class="who"><span class="avatar" role="img" aria-label="Reviewer avatar"></span><div><b>RICHARD</b><small>London</small></div></div><div class="stars">★★★★★</div><p>Lorem ipsum dolor sit amet, consectetur adipiscing elit, sed do eiusmod tempor incididunt ut labore et dolore magna aliqua. Ut enim ad minim veniam, quis nostrud exercitation ullamco laboris nisi ut aliquip ex ea commodo consequat. Duis aute irure dolo.</p></div>
<div class="review abs" style="left:449px;top:3061px"><div class="who"><span class="avatar" role="img" aria-label="Reviewer avatar"></span><div><b>RICHARD</b><small>London</small></div></div><div class="stars">★★★★★</div><p>Lorem ipsum dolor sit amet, consectetur adipiscing elit, sed do eiusmod tempor incididunt ut labore et dolore magna aliqua. Ut enim ad minim veniam, quis nostrud exercitation ullamco laboris nisi ut aliquip ex ea commodo consequat. Duis aute irure dolo.</p></div>
<div class="review abs" style="left:768px;top:3061px"><div class="who"><span class="avatar" role="img" aria-label="Reviewer avatar"></span><div><b>RICHARD</b><small>London</small></div></div><div class="stars">★★★★★</div><p>Lorem ipsum dolor sit amet, consectetur adipiscing elit, sed do eiusmod tempor incididunt ut labore et dolore magna aliqua. Ut enim ad minim veniam, quis nostrud exercitation ullamco laboris nisi ut aliquip ex ea commodo consequat. Duis aute irure dolo.</p></div>

<footer class="site-footer abs">
  <div class="brand">BorrowNest</div>
  <div class="follow">Follow us <i></i><i></i><i></i><i></i></div>
  <nav class="foot-nav"><span>Home</span><span>About Us</span><span>Our People</span><span>Loan Options</span><span>Calculators</span><span>Reviews</span><span>Contact Us</span></nav>
  <div class="copy">Copyright © 2022 All Rights Reserved</div>
</footer>

</body>
</html>
```